Vindgerdi - Start-up company selling electricity

Hello let me tell you about Vindgerdi.

Vindgerdi is start-up company selling electricity in Iceland. The operations of the company consist of making power usage forecasts for our customers, purchasing the electricity wholesale from the energy producers, and selling the electricity to the consumer. We are focused on tech by using optimization and machine learning to minimize electricity prices to our customers. Our marketing strategy is to portray a tech company mindset and to show dedication to driving down the electricity price on the market.

We need your help to make our website pop. Possible concepts to work with are as follows:

- Iceland the land of ice and fire
- Green energy
- Innovation
- Tech and data science

Link to our website: https://prufa.vindgerdi-example.is/
We are open to ideas.
Thank you!

Target Market(s)

Electricity consumers both homes and companies.

Number of Pages Required

1 page

Font styles to use
Serif
Sans Serif

```html
<!DOCTYPE html>
<html lang="is">
<head>
<meta charset="utf-8">
<title>Vindgerdi</title>
<link href="https://fonts.googleapis.com/css2?family=Exo:wght@400;500&family=Karla:wght@400&family=Cinzel:wght@500&family=Arimo:wght@400&display=swap" rel="stylesheet">
<style>
:root{
  --orange:#f25a0c;
  --green:#7f9e07;
  --ink:#222;
  --dark:#333333;
  --card-line:#a9a9ab;
  --hero-a:#0b2440;
  --hero-b:#2f7fb4;
  --hero-c:#7fd0ee;
  --white:#fff;
}
*{margin:0;padding:0;box-sizing:border-box}
html,body{width:1083px;height:1200px;overflow:hidden;background:var(--white)}
body{position:relative;font-family:"Karla",sans-serif;color:var(--ink)}
h1,h2{font-weight:400}
.site-header{position:absolute;left:0;top:0;width:1083px;height:103px;background:var(--white)}
.brand{position:absolute;left:127px;top:30px;display:flex;align-items:center;gap:10px}
.brand-dot{width:26px;height:26px;border-radius:50%;background:var(--orange)}
.brand-name{font-family:"Exo",sans-serif;font-weight:400;font-size:35px;color:var(--orange);letter-spacing:1px;line-height:1}
.main-nav a{position:absolute;top:43px;font-family:"Exo",sans-serif;font-size:13px;color:#444;text-decoration:none;letter-spacing:.3px}
.hero{position:absolute;left:0;top:103px;width:1083px;height:350px;
  background:radial-gradient(circle at 78% 45%,var(--hero-c) 0%,var(--hero-b) 35%,var(--hero-a) 85%)}
.hero-title{position:absolute;left:119px;top:175px;width:299px;height:124px;background:var(--green);
  padding:22px 0 0 12px;font-family:"Exo",sans-serif;font-weight:400;font-size:29px;line-height:40px;color:var(--white);letter-spacing:.8px}
.towers{position:absolute;left:0;top:453px;width:1083px;height:536px;background:linear-gradient(#fff,#f6f6f6 60%,#fafafa)}
.card{position:absolute;top:396px;width:266px;height:352px;background:var(--white);border-bottom:2px solid var(--card-line);
  box-shadow:0 0 2px rgba(0,0,0,.12);text-align:center}
.card-icon{position:absolute;left:78px;top:27px;width:110px;height:110px;border:1.5px dotted #999;border-radius:50%;
  display:flex;align-items:center;justify-content:center}
.card-title{position:absolute;left:0;right:0;top:148px;font-family:"Exo",sans-serif;font-weight:400;font-size:14px;color:#111;letter-spacing:.3px}
.card-text{position:absolute;left:18px;right:18px;top:180px;font-size:11.2px;line-height:17.2px;color:#222}
.btn{position:absolute;top:293px;width:102px;height:35px;display:flex;align-items:center;justify-content:center;
  font-family:"Cinzel",serif;font-weight:500;font-size:11px;letter-spacing:1px;color:var(--white)}
.btn-green{background:var(--green)}
.btn-orange{background:var(--orange)}
.prices{position:absolute;left:0;right:0;top:183px;height:72px}
.price{position:absolute;top:0;width:120px;text-align:center;font-size:11px;line-height:14px}
.price-value{font-family:"Arimo",sans-serif;font-size:17px;line-height:26px;color:#111}
.price-divider{position:absolute;left:129px;top:0;width:1px;height:70px;background:#e3e3e3}
.compare{position:absolute;left:0;right:0;top:264px;font-size:11px}
.site-footer{position:absolute;left:0;top:989px;width:1083px;height:172px;background:var(--dark);color:var(--white)}
.footer-icon{position:absolute;top:35px;width:35px;height:35px;border:1px solid var(--orange);display:flex;align-items:center;justify-content:center}
.footer-text{position:absolute;top:36px;font-family:"Exo",sans-serif;font-size:13px;line-height:19px;letter-spacing:.3px}
.footer-brand{position:absolute;left:0;right:0;top:40px;display:flex;justify-content:center;align-items:center;gap:8px}
.footer-brand .brand-dot{width:18px;height:18px}
.footer-brand .brand-name{font-size:24px}
.footer-legal{position:absolute;left:0;right:0;top:124px;text-align:center;font-family:"Exo",sans-serif;font-size:12px;line-height:17px}
.copyright{position:absolute;left:0;top:1161px;width:1083px;height:39px;background:var(--orange);color:var(--white);
  display:flex;align-items:center;justify-content:center;font-size:11.5px}
</style>
</head>
<body>
<header class="site-header">
  <div class="brand"><span class="brand-dot"></span><span class="brand-name">VINDGERDI</span></div>
  <nav class="main-nav">
    <a href="#" style="left:545px">Viðskiptaskilmálar</a>
    <a href="#" style="left:708px">Spurt &amp; Svarað</a>
    <a href="#" style="left:841px">Um Vindgerdi</a>
  </nav>
</header>

<section class="hero" role="img" aria-label="Hand touching a glowing digital globe covered in a network of connected points"></section>
<h1 class="hero-title">SAMA RAFMAGN<br>BARA ÓDÝRARA!</h1>

<div class="towers" role="img" aria-label="Faint line drawing of electricity pylons"></div>

<article class="card" style="left:127px">
  <div class="card-icon">
    <svg width="40" height="60" viewBox="0 0 40 60" fill="none" stroke="#7f9e07" stroke-width="2.5" stroke-linecap="round" stroke-linejoin="round">
      <path d="M12 2v10M28 2v10M4 12h32v12a16 16 0 0 1-32 0z"/><path d="M22 22l-5 7h7l-5 7"/><path d="M20 40v8a8 8 0 0 0 8 8"/>
    </svg>
  </div>
  <h2 class="card-title">Velkomin Í Viðskipti</h2>
  <p class="card-text">Lorem ipsum dolor sit a consectetuer adipiscing elit, sed diam nonummy nibh euismod tincidunt ut laoreet dolore magna aliquam erat volutpat.Ut wisi enim ad minim veniam quis.</p>
  <a class="btn btn-green" style="left:24px">FYRIRTÆKI</a>
  <a class="btn btn-orange" style="left:132px">HEIMILI</a>
</article>

<article class="card" style="left:408px">
  <div class="card-icon">
    <svg width="46" height="58" viewBox="0 0 46 58" fill="none" stroke="#7f9e07" stroke-width="2.2" stroke-linejoin="round">
      <path d="M2 2h34l8 8v46H2z"/><path d="M10 10h6M10 14h6M30 10h6M30 14h6M23 6v14M27 9h-6v4h4v4h-6"/>
      <rect x="9" y="24" width="6" height="6"/><rect x="9" y="34" width="6" height="6"/><rect x="9" y="44" width="6" height="6"/>
      <path d="M20 26h16M20 29h16M20 36h16M20 39h16M20 46h16M20 49h16"/>
    </svg>
  </div>
  <h2 class="card-title">Verðskrá</h2>
  <div class="prices">
    <div class="price" style="left:3px"><div class="price-value">6.95</div>krónur / kWst</div>
    <span class="price-divider"></span>
    <div class="price" style="left:138px"><div class="price-value">6.22</div>krónur / kWst<br>rafmagnskynding</div>
  </div>
  <p class="compare">Gerðu verðsamanburð</p>
  <a class="btn btn-green" style="left:83px">VERÐVAKT</a>
</article>

<article class="card" style="left:689px">
  <div class="card-icon">
    <svg width="44" height="68" viewBox="0 0 44 68" fill="none" stroke="#7f9e07" stroke-width="3.5" stroke-linejoin="round">
      <path d="M28 2L4 40h16l-6 26 28-38H26z"/>
    </svg>
  </div>
  <h2 class="card-title">Framtíðin Er Spennandi</h2>
  <p class="card-text">Gerum raforkukerfið snallara saman. Vindgerdi notar gervigreind, gagnavísindi og sjálfvirkni til að lágmarka kostnað og stuðla að okrujöfnuði</p>
  <a class="btn btn-green" style="left:93px;top:291px">VITA MEIRA</a>
</article>

<footer class="site-footer">
  <div class="footer-icon" style="left:127px">
    <svg width="22" height="16" viewBox="0 0 22 16" fill="none" stroke="#7f9e07" stroke-width="1.3"><rect x="1" y="1" width="20" height="14"/><path d="M1 1l10 8 10-8"/></svg>
  </div>
  <p class="footer-text" style="left:176px">vindgerdi@vindgerdi-example.is<br>400-1234</p>
  <div class="footer-brand"><span class="brand-dot"></span><span class="brand-name">VINDGERDI</span></div>
  <div class="footer-icon" style="left:718px">
    <svg width="14" height="20" viewBox="0 0 14 20" fill="none" stroke="#7f9e07" stroke-width="1.3"><path d="M7 19S1 11 1 7a6 6 0 0 1 12 0c0 4-6 12-6 12z"/><circle cx="7" cy="7" r="2.3"/></svg>
  </div>
  <p class="footer-text" style="left:769px">HEIMILISFANG<br>Dæmigötu 7 170 Seltjarnarnesi</p>
  <p class="footer-legal">Vindgerdi Ehf<br>Kennitala: 510101-2290 &nbsp;&nbsp; • &nbsp;&nbsp; Vskm Númer: 123456</p>
</footer>
<div class="copyright">Copyright © Vindgerdi 2021 Allur Réttur Áskilin</div>
</body>
</html>
```